The design should look similar to the uploaded example to accommodate the information needed for a business card template. I would like to see the colors orange and charcoal grey incorporated along with the logo.The following should be on the back of the card SPECIALIZING IN NEW AND USED TIRES & WHEELS FOR:- Loaders- Skid Steers- Telehandlers- Boom Lifts- Forklifs and moreELIMINATING DOWNTIMEWheel Exchange Program for New & Used Foam Filled and Solid Rubber TiresSPECIALTY SERVICES- Foam Filling Tires- Largest Tire Press in SE- ONSITE Forklift Tire Press- Boom Truck Services - Rubber Tracks

Target Market(s)

New and Existing Customers

Industry/Entity Type

Business

Contact Information for Business Card

NAMEHEAVY DUTY TIRE, LLC8470 Belvedere RoadWest Palm Beach, FL 33411P: 844-HD-TIRESF: 561-431-6469C:E: W: WWW.GRANITERIMSUPPLY-EXAMPLE.COM

Font styles to use
Sans Serif

Colors
f37122
333333

Requirements
Must have
• The logo and the information indicated for the backside of the card
Nice to have
• Keep the orange and charcoal grey colors

```html
<!DOCTYPE html>
<html lang="en">
<head>
<meta charset="utf-8">
<title>Granite Rim Supply – Business Card</title>
<link rel="stylesheet" href="https://fonts.googleapis.com/css2?family=Source+Sans+3:wght@400;600;700&display=swap">
<style>
  :root {
    --orange: #f37122;
    --charcoal: #333333;
    --card: #111111;
    --backdrop: #3a3532;
    --white: #f2f2f2;
  }
  * { box-sizing: border-box; margin: 0; padding: 0; }
  html, body { width: 1200px; height: 844px; overflow: hidden; }
  body {
    background: var(--backdrop);
    font-family: "Source Sans 3", Arial, sans-serif;
    color: var(--white);
    position: relative;
  }
  .card {
    position: absolute;
    top: 262px;
    width: 550px;
    height: 314px;
    background: var(--card);
    box-shadow: 0 8px 24px rgba(0,0,0,.45);
  }
  .card--front { left: 40px; }
  .card--back { left: 610px; }

  /* Front */
  .brand {
    position: absolute;
    left: 150px; top: 36px;
    display: flex; align-items: center; gap: 12px;
  }
  .brand__mark {
    width: 66px; height: 66px; border-radius: 50%;
    background: var(--orange);
  }
  .brand__name {
    font-weight: 700; font-size: 22px; color: var(--orange);
    letter-spacing: .5px;
  }
  .identity {
    position: absolute; left: 32px; bottom: 34px;
    line-height: 1.3;
  }
  .identity__name { font-size: 21px; font-weight: 600; color: var(--orange); margin-bottom: 16px; }
  .identity__company { font-size: 18px; font-weight: 600; color: var(--orange); }
  .identity__address { font-size: 17px; }
  .contact {
    position: absolute; right: 28px; top: 150px;
    list-style: none; text-align: right;
    font-size: 14.5px; line-height: 1.62;
  }
  .contact li { display: flex; justify-content: flex-end; align-items: center; gap: 8px; }
  .contact svg { width: 11px; height: 11px; fill: var(--orange); flex: none; }

  /* Back */
  .services {
    position: absolute; left: 20px; right: 20px; top: 40px;
    text-align: center; line-height: 1.4;
  }
  .services__heading { color: var(--orange); font-weight: 700; font-size: 17px; text-transform: uppercase; }
  .services__heading--small { font-size: 13.5px; margin-top: 12px; }
  .services__heading--mid { font-size: 18px; margin-top: 14px; }
  .services__line { font-size: 15px; font-weight: 600; }
  .dot {
    display: inline-block; width: 6px; height: 6px; border-radius: 50%;
    background: var(--orange); margin: 0 8px; vertical-align: middle;
  }
</style>
</head>
<body>
  <section class="card card--front" aria-label="Card front">
    <div class="brand">
      <span class="brand__mark"></span>
      <span class="brand__name">GRANITE RIM</span>
    </div>
    <ul class="contact">
      <li>844-GR-WHEEL <svg viewBox="0 0 12 12"><path d="M2 1h3l1 3-2 1a7 7 0 0 0 3 3l1-2 3 1v3a1 1 0 0 1-1 1A10 10 0 0 1 1 2a1 1 0 0 1 1-1z"/></svg></li>
      <li>561-278-9053 <svg viewBox="0 0 12 12"><rect x="1" y="3" width="10" height="8" rx="1"/><rect x="3" y="0" width="6" height="3"/></svg></li>
      <li>561-390-4417 <svg viewBox="0 0 12 12"><path d="M3 0h6a1 1 0 0 1 1 1v10a1 1 0 0 1-1 1H3a1 1 0 0 1-1-1V1a1 1 0 0 1 1-1zm0 2v8h6V2z"/></svg></li>
      <li>info@graniterimsupply-example.com <svg viewBox="0 0 12 12"><path d="M0 2h12v8H0zm1 1 5 4 5-4z"/></svg></li>
      <li>www.graniterimsupply-example.com <svg viewBox="0 0 12 12"><circle cx="6" cy="6" r="6"/></svg></li>
    </ul>
    <div class="identity">
      <p class="identity__name">Dalton Reeves</p>
      <p class="identity__company">GRANITE RIM SUPPLY, LLC</p>
      <p class="identity__address">5126 Marston Lane</p>
      <p class="identity__address">Lake Harlow, FL 33490</p>
    </div>
  </section>

  <section class="card card--back" aria-label="Card back">
    <div class="services">
      <h2 class="services__heading">Specializing in new and used tires &amp; wheels for:</h2>
      <p class="services__line">Loaders<span class="dot"></span>Skid Steers<span class="dot"></span>Telehandlers<span class="dot"></span>Boom Lifts</p>
      <p class="services__line">Forklifs and more</p>
      <h3 class="services__heading services__heading--small">Eliminating Downtime</h3>
      <p class="services__line">Wheel Exchange Program for New &amp; Used Foam</p>
      <p class="services__line">Filled and Solid Rubber Tires</p>
      <h3 class="services__heading services__heading--mid">Specialty Services</h3>
      <p class="services__line">Foam Filling Tires<span class="dot"></span>Largest Tire Press in SE</p>
      <p class="services__line">ONSITE Forklift Tire Press<span class="dot"></span>Boom Truck Services<span class="dot"></span>Rubber Tracks</p>
    </div>
  </section>
</body>
</html>
```